Homeowners Insurance Provider Website

We are selling homeowners insurance policy / tenants Policy/Flood Insurance in USA in few states and planning expand nationally.

Our target audience are two folds: Customers (Buy policies) and Insurance Agents who wants to work with us to sell our policies to customers. But website should focus 80% on customers and 20% on agents. So, more customer focused user experience. Please note that there is no direct buy option for customers. They always go through insurance agents.

Customer focused, educational that makes buyer journey easy. We don’t want to come off as trying sell something as there is no direct sales involved from website.

Target Market(s)

Homeowners in USA and Insurance agent who sells these insurance.

Industry/Entity Type

Insurance

Number of Pages Required

4 page

Font styles to use
Other font styles liked:
• Open to suggestions

Colors

Designer to choose colors to be used in the design.

Requirements
Must have
• Three most important things: Trustworthy, Authentic, Simple
• Please use colors form logo and grays
• We like: www.hollowmere.com
• https://www.quillfenbrook.com/
• We need Agent Look up tool on home page similar to what is shown on example sites.
• Design:
• Home Page - Open to Ideas
• Insurance (Products) Landing Page - Info similar to: https://www.quillfenbrook.com/insurance/
• Agents Page - https://www.quillfenbrook.com/agents/
• Claims Page - Information similar to: https://www.quillfenbrook.com/claims-center/
• Site Navigation:
• Home
• Insurance
• Claims
• Agents
• About Us
• Contact Us
Nice to have
• Elegant, minimal and clean design that reflects trust and authenticity.
Should not have
• Slider or rotating images - prefer flat design. Not over powering design.

```html
<!DOCTYPE html>
<html lang="en">
<head>
<meta charset="utf-8">
<title>Hearthline Insurance Co.</title>
<link href="https://fonts.googleapis.com/css2?family=Lato:ital,wght@0,400;0,700;0,900;1,400;1,700&family=Montserrat:wght@500;600;700&display=swap" rel="stylesheet">
<style>
:root{
  --blue:#253f87;
  --blue-dark:#1c3270;
  --red:#d3212f;
  --ink:#2b2b2b;
  --text:#555;
  --grey-bg:#f4f4f4;
  --line:#dedede;
  --white:#fff;
}
*{box-sizing:border-box;margin:0;padding:0}
html,body{width:1200px;height:2961px;overflow:hidden}
body{position:relative;font-family:'Lato',sans-serif;color:var(--text);background:var(--white)}
.abs{position:absolute}
a{color:inherit}

/* header */
.site-header{top:0;left:0;width:1200px;height:76px;background:var(--white)}
.brand{left:140px;top:10px;display:flex;align-items:center;gap:10px}
.brand-mark{width:46px;height:52px;background:var(--blue);border-radius:4px}
.brand-name{font-family:'Montserrat',sans-serif;font-weight:700;font-size:24px;line-height:1;color:var(--blue)}
.brand-name small{display:block;font-size:15px;font-weight:500;letter-spacing:3px;margin-top:3px}
.header-phone{left:682px;top:20px;display:flex;align-items:center}
.icon-box{width:30px;height:30px;background:var(--red);border-radius:4px;display:flex;align-items:center;justify-content:center;flex:none}
.header-phone .num{background:#efefef;height:30px;line-height:30px;padding:0 16px;font-size:15px;color:var(--ink);font-weight:700;margin-left:6px;white-space:nowrap}
.consult{left:856px;top:20px;display:flex;align-items:center}
.consult .label{background:var(--blue);color:#fff;font-family:'Montserrat',sans-serif;font-size:10.5px;font-weight:600;height:32px;line-height:32px;padding:0 12px;margin-left:6px;white-space:nowrap;text-transform:uppercase}

.main-nav{top:76px;left:0;width:1200px;height:42px;background:var(--blue)}
.main-nav ul{list-style:none;position:absolute;left:140px;top:0;display:flex}
.main-nav li{height:42px;line-height:42px;font-family:'Montserrat',sans-serif;font-size:12px;font-weight:600;color:#fff;text-transform:uppercase;text-align:center;border-right:1px solid rgba(255,255,255,.25)}
.main-nav li:last-child{border-right:0}
.main-nav li.active{background:var(--red)}

/* hero */
.hero{top:118px;left:0;width:1200px;height:494px;background:linear-gradient(100deg,#e9edf0 0%,#d9dfe4 35%,#6f7a86 62%,#2d3644 100%)}
.hero-text{left:140px;top:242px;width:450px;font-family:'Montserrat',sans-serif;font-weight:700;font-size:18.5px;line-height:34px;color:#2b2b2b;text-transform:uppercase}
.agent-lookup{left:140px;top:400px;display:flex;align-items:center;gap:0}
.agent-lookup .lookup-label{font-family:'Montserrat',sans-serif;font-weight:700;font-size:13px;color:var(--blue);text-transform:uppercase;margin-right:14px;white-space:nowrap}
.agent-lookup .lookup-field{width:190px;height:36px;background:#fff;border:1px solid #c9cfd6;font-size:13px;line-height:34px;padding-left:12px;color:#888}
.agent-lookup .lookup-btn{height:36px;line-height:36px;width:96px}

/* welcome */
.welcome-title{top:678px;left:0;width:1200px;text-align:center;font-family:'Montserrat',sans-serif;font-weight:700;font-size:29px;color:var(--blue);line-height:1}
.welcome-title span{font-weight:500}
.welcome-title small{display:block;font-size:16px;font-weight:500;letter-spacing:4px;margin:4px 0 0 236px}
.welcome-copy{top:764px;left:164px;width:872px;text-align:center;font-size:12.5px;line-height:23px;color:#555}
.btn{display:inline-block;background:var(--red);color:#fff;font-family:'Montserrat',sans-serif;font-weight:600;font-size:14px;text-transform:uppercase;text-align:center;text-decoration:none}
.read-more{left:529px;top:882px;width:142px;height:36px;line-height:36px}

/* services */
.service{color:#fff;text-align:center}
.service.flood{left:0;top:1000px;width:392px;height:445px;background:linear-gradient(160deg,#d8434e,#c51f2e);clip-path:polygon(0 0,100% 2%,100% 100%,50% 86%,0 88%)}
.service.policy{left:400px;top:976px;width:400px;height:580px;background:linear-gradient(170deg,#2f4c96,#243e84);clip-path:polygon(0 4%,50% 0,100% 4%,100% 91%,50% 100%,0 91%)}
.service.tenants{left:808px;top:985px;width:392px;height:460px;background:linear-gradient(200deg,#e04f55,#c9232f);clip-path:polygon(0 0,100% 0,100% 88%,50% 86%,0 100%)}
.svc-icon{position:absolute;width:112px;height:112px;border:2px solid #fff;top:var(--t);left:50%;transform:translateX(-50%);display:flex;align-items:center;justify-content:center}
.svc-title{position:absolute;left:0;width:100%;font-family:'Montserrat',sans-serif;font-weight:700;font-size:18px;letter-spacing:.5px;text-transform:uppercase}
.svc-copy{position:absolute;left:50%;transform:translateX(-50%);font-size:14px;line-height:24px}
.svc-link{position:absolute;left:0;width:100%;font-size:13px;font-weight:700;font-style:italic;text-decoration:underline;text-transform:uppercase}

/* testimonials */
.section-title{left:0;width:1200px;text-align:center;font-family:'Montserrat',sans-serif;font-weight:700;font-size:29px;color:var(--blue);text-transform:uppercase}
.section-title span{font-weight:500}
.testimonial-card{left:140px;top:1760px;width:918px;height:132px;border:1px solid var(--line);background:#fff}
.avatar{left:156px;top:1712px;width:122px;height:130px;background:linear-gradient(160deg,#c9b7a6,#7e6a5b);clip-path:polygon(50% 0,100% 14%,100% 86%,50% 100%,0 86%,0 14%)}
.client-name{left:288px;top:1734px;font-family:'Montserrat',sans-serif;font-weight:700;font-size:13px;color:var(--blue);text-transform:uppercase}
.stars{left:166px;top:1854px;display:flex;gap:4px}
.quote{left:330px;top:1786px;width:702px;font-size:12px;font-style:italic;line-height:23px;color:#444}
.qmark{font-family:Georgia,serif;font-size:46px;color:#c8c8c8;line-height:1}
.arrow{top:1812px}

/* cta section */
.cta-band{left:0;top:1955px;width:1200px;height:640px;background:var(--grey-bg)}
.cta-photo{top:2025px;width:438px;height:226px}
.cta-photo.claims{left:140px;background:linear-gradient(150deg,#dfe3e8,#9aa5b3 60%,#5e6a78)}
.cta-photo.agents{left:620px;background:linear-gradient(150deg,#eef0ef,#c8c2b8 55%,#8d8579)}
.cta-title{top:2285px;width:438px;text-align:center;font-family:'Montserrat',sans-serif;font-weight:700;font-size:21px;color:var(--blue);text-transform:uppercase}
.cta-copy{top:2328px;width:438px;text-align:center;font-size:13.5px;line-height:23px;color:#444}
.cta-btn{top:2425px;height:36px;line-height:36px;width:148px}
.become{left:786px;top:2465px;width:106px;text-align:center;font-size:12px;color:var(--ink);text-decoration:underline}

/* footer */
.footer{left:0;top:2595px;width:1200px;height:310px;background:linear-gradient(180deg,#3a3f47,#23272d 60%,#1b1e23)}
.footer-head{font-family:'Montserrat',sans-serif;font-weight:700;font-size:17px;color:#fff;text-transform:uppercase;letter-spacing:.5px;white-space:nowrap}
.quick-links{left:142px;top:2680px}
.quick-links ul{list-style:none;margin-top:28px}
.quick-links li{color:#fff;font-size:12px;line-height:28.5px;padding-left:14px;position:relative}
.quick-links li::before{content:"";position:absolute;left:0;top:12px;width:5px;height:5px;border-radius:50%;background:#fff}
.contact{left:368px;top:2680px;width:280px}
.contact-row{display:flex;gap:12px;color:#fff;font-size:12px;line-height:19px;position:absolute;left:0;white-space:nowrap}
.contact-row strong{font-family:'Montserrat',sans-serif;font-size:13px;font-weight:600;text-transform:uppercase}
.contact-row .sub{color:#c9c9c9}
.inquiry{left:680px;top:2550px;width:398px;height:385px;background:var(--blue);clip-path:polygon(6% 3%,50% 0,94% 3%,100% 6%,100% 94%,50% 100%,0 94%,0 6%)}
.inquiry-title{position:absolute;top:66px;width:100%;text-align:center;font-family:'Montserrat',sans-serif;font-weight:600;font-size:17px;color:#fff;text-transform:uppercase}
.inquiry-rule{position:absolute;top:102px;left:20px;right:20px;height:1px;background:rgba(255,255,255,.2)}
.field{position:absolute;left:20px;width:358px;height:28px;border:1px solid rgba(255,255,255,.65);color:#fff;font-size:11px;line-height:26px;padding-left:8px}
.submit{position:absolute;left:131px;top:316px;width:116px;height:46px;background:var(--red);color:#fff;font-family:'Montserrat',sans-serif;font-weight:700;font-size:17px;text-transform:uppercase;text-align:center;line-height:36px;clip-path:polygon(0 0,100% 0,100% 70%,50% 100%,0 70%)}
.bottom-bar{left:0;top:2905px;width:1200px;height:56px;background:var(--blue)}
.copyright{position:absolute;left:140px;top:22px;color:#fff;font-size:11px}
.social{position:absolute;left:614px;top:14px;display:flex;gap:10px}
.social span{width:28px;height:28px;border:1.5px solid #fff;border-radius:50%}
</style>
</head>
<body>

<header class="site-header abs">
  <div class="brand abs">
    <div class="brand-mark"></div>
    <div class="brand-name">HEARTHLINE<small>INSURANCE CO.</small></div>
  </div>
  <div class="header-phone abs">
    <div class="icon-box"><svg width="16" height="16" viewBox="0 0 24 24"><path fill="#fff" d="M6.6 10.8a15 15 0 0 0 6.6 6.6l2.2-2.2a1 1 0 0 1 1-.25 11.4 11.4 0 0 0 3.6.57 1 1 0 0 1 1 1V20a1 1 0 0 1-1 1A17 17 0 0 1 3 4a1 1 0 0 1 1-1h3.5a1 1 0 0 1 1 1c0 1.25.2 2.45.57 3.57a1 1 0 0 1-.25 1z"/></svg></div>
    <span class="num">012-555-0193</span>
  </div>
  <div class="consult abs">
    <div class="icon-box"><svg width="16" height="16" viewBox="0 0 24 24" fill="none" stroke="#fff" stroke-width="2"><path d="M4 5h12v8H9l-4 3v-3H4z"/><path d="M18 9h2v8h-1v3l-4-3h-4"/></svg></div>
    <span class="label">Get a free consultation</span>
  </div>
</header>

<nav class="main-nav abs">
  <ul>
    <li class="active" style="width:110px">Home</li>
    <li style="width:142px">About Us</li>
    <li style="width:145px">Insurance</li>
    <li style="width:142px">Claims</li>
    <li style="width:152px">Agents</li>
    <li style="width:140px">Contact Us</li>
  </ul>
</nav>

<section class="hero abs" role="img" aria-label="Photo of two businessmen reviewing documents at a desk with a laptop"></section>
<p class="hero-text abs">We are selling homeowners insurance policy / tenants policy/ flood insurance in USA in few states and planning to expand nationally.</p>
<form class="agent-lookup abs" role="search" aria-label="Agent lookup">
  <span class="lookup-label">Find an Agent</span>
  <div class="lookup-field">Enter ZIP Code</div>
  <span class="btn lookup-btn">Search</span>
</form>

<h1 class="welcome-title abs">WELCOME TO <span>HEARTHLINE</span><small>INSURANCE CO.</small></h1>
<p class="welcome-copy abs">Lorem ipsum dolor sit amet, consectetuer adipiscing elit, sed diam nonummy nibh euismod tincidunt ut laoreet dolore magna aliquam erat volutpat. Ut wisi enim ad minim veniam, quis nostrud exerci tation ullamcorper suscipit lobortis nisl ut aliquip ex ea commodo consequat. Duis autem vel eum iriure dolor in hendrerit in vulputate velit esse molestie consequat, vel illum dolore eu feugiat nulla facilisis at vero eros et accumsan et iusto odio dignissim qui blandit praesent luptatum zzril delenit augue duis dolore te feugait nulla facilisi.</p>
<a class="btn read-more abs">Read More</a>

<section class="service flood abs" role="img" aria-label="Red-tinted photo of a house and umbrella">
  <div class="svc-icon" style="--t:60px"><svg width="58" height="58" viewBox="0 0 58 58" fill="none" stroke="#fff" stroke-width="2.5"><path d="M8 28 29 10l21 18"/><path d="M14 24v14h30V24"/><rect x="25" y="28" width="8" height="10"/><path d="M6 44c4-3 7-3 11 0s7 3 11 0 7-3 11 0 7 3 11 0"/><path d="M6 51c4-3 7-3 11 0s7 3 11 0 7-3 11 0 7 3 11 0"/></svg></div>
  <h2 class="svc-title" style="top:212px">Flood Insurance</h2>
  <p class="svc-copy" style="top:268px;width:260px">Lorem ipsum dolor sit amet, consectetuer pmbe adipiscing elit, sed diam nonummy nibh euistincidunt.</p>
  <a class="svc-link" style="top:352px">Read More »</a>
</section>

<section class="service policy abs" role="img" aria-label="Blue-tinted photo of an insurance policy document">
  <div class="svc-icon" style="--t:84px"><svg width="58" height="58" viewBox="0 0 58 58" fill="none" stroke="#fff" stroke-width="2.5"><path d="M6 28a23 21 0 0 1 46 0c-3-3-7-3-11 0-3-3-8-3-12 0-4-3-9-3-12 0-4-3-8-3-11 0z"/><path d="M29 7v3M29 28v18a4 4 0 0 1-8 0"/></svg></div>
  <h2 class="svc-title" style="top:236px">Insurance Policy</h2>
  <p class="svc-copy" style="top:292px;width:280px">Lorem ipsum dolor sit amet, consectetuer pmbe adipiscing elit, sed diam nonummy nibh euistincidunt Lorem ipsum dolor sit amet, consectetuer pmbe adipiscing elit, sed diam nonummy nibh euistincidunt.</p>
  <a class="svc-link" style="top:448px">Read More »</a>
</section>

<section class="service tenants abs" role="img" aria-label="Red-tinted photo of a family in front of their home">
  <div class="svc-icon" style="--t:75px"><svg width="58" height="58" viewBox="0 0 58 58" fill="none" stroke="#fff" stroke-width="2.5"><path d="M20 22 33 11l13 11v12H20z"/><rect x="29" y="26" width="7" height="8"/><path d="M6 40h8l10 4h12a3 3 0 0 1 0 6H22"/><path d="M36 46l12-6a3 3 0 0 1 3 5L38 52H14"/></svg></div>
  <h2 class="svc-title" style="top:227px">Tenants Policy</h2>
  <p class="svc-copy" style="top:283px;width:260px">Lorem ipsum dolor sit amet, consectetuer pmbe adipiscing elit, sed diam nonummy nibh euistincidunt.</p>
  <a class="svc-link" style="top:367px">Read More »</a>
</section>

<h2 class="section-title abs" style="top:1632px">Clients <span>Testimonials</span></h2>
<svg class="arrow abs" style="left:104px" width="14" height="22" viewBox="0 0 14 22"><path d="M11 2 3 11l8 9" fill="none" stroke="#c4c4c4" stroke-width="2"/></svg>
<svg class="arrow abs" style="left:1074px" width="14" height="22" viewBox="0 0 14 22"><path d="M3 2l8 9-8 9" fill="none" stroke="#c4c4c4" stroke-width="2"/></svg>
<div class="testimonial-card abs"></div>
<div class="avatar abs" role="img" aria-label="Portrait photo of the client"></div>
<p class="client-name abs">- Mr. Talven Orrick</p>
<div class="stars abs">
  <svg width="16" height="16" viewBox="0 0 24 24"><path fill="#d3212f" d="M12 2l3 7 7 .6-5.4 4.7 1.7 7.2L12 17.8 5.7 21.5l1.7-7.2L2 9.6 9 9z"/></svg>
  <svg width="16" height="16" viewBox="0 0 24 24"><path fill="#d3212f" d="M12 2l3 7 7 .6-5.4 4.7 1.7 7.2L12 17.8 5.7 21.5l1.7-7.2L2 9.6 9 9z"/></svg>
  <svg width="16" height="16" viewBox="0 0 24 24"><path fill="#d3212f" d="M12 2l3 7 7 .6-5.4 4.7 1.7 7.2L12 17.8 5.7 21.5l1.7-7.2L2 9.6 9 9z"/></svg>
  <svg width="16" height="16" viewBox="0 0 24 24"><path fill="#d3212f" d="M12 2l3 7 7 .6-5.4 4.7 1.7 7.2L12 17.8 5.7 21.5l1.7-7.2L2 9.6 9 9z"/></svg>
  <svg width="16" height="16" viewBox="0 0 24 24"><path fill="#d3212f" d="M12 2l3 7 7 .6-5.4 4.7 1.7 7.2L12 17.8 5.7 21.5l1.7-7.2L2 9.6 9 9z"/></svg>
</div>
<span class="qmark abs" style="left:290px;top:1778px">“</span>
<p class="quote abs">Lorem ipsum dolor sit amet, consectetuer adipiscing elit, sed diam nonummy nibh euismod tincidunt ut laoreet dolore magna aliquam erat volutpat. Ut wisi enim ad minim veniam, quis nostrud exerci tation ullamcorper suscipit lobortis nisl ut aliquip ex ea commodo. Ut wisi enim ad minim veniam, quis nostrud exerci tation ullamcorper suscipit lobortis nisl ut aliquip ex ea commodo.</p>
<span class="qmark abs" style="left:874px;top:1834px">”</span>

<section class="cta-band abs"></section>
<div class="cta-photo claims abs" role="img" aria-label="Photo of an insurance claim form with glasses, pen and calculator"></div>
<div class="cta-photo agents abs" role="img" aria-label="Photo of an agent meeting a couple at a table"></div>
<h3 class="cta-title abs" style="left:140px">Claims Process</h3>
<p class="cta-copy abs" style="left:140px;padding:0 36px">Accidents are stressful, but reporting and viewing your claim shouldn't be. Whether you need to report a claim or check an existing one, Hearthline Insurance Company can help.</p>
<a class="btn cta-btn abs" style="left:285px">Get Started</a>
<h3 class="cta-title abs" style="left:620px">For Agents</h3>
<p class="cta-copy abs" style="left:620px;padding:0 26px">Whether you're a seasoned insurance agent looking to expand your agency or are new to the industry, we're ready to help you help others.</p>
<a class="btn cta-btn abs" style="left:765px">Agent Login</a>
<a class="become abs">Become an Agent</a>

<footer class="footer abs" role="img" aria-label="Darkened photo of a city skyline"></footer>
<div class="quick-links abs">
  <h4 class="footer-head">Quick Links</h4>
  <ul><li>Home</li><li>About Us</li><li>Insurance</li><li>Claims</li><li>Agents</li><li>Contact Us</li></ul>
</div>
<div class="contact abs">
  <h4 class="footer-head">Contact Details</h4>
  <div class="contact-row" style="top:48px">
    <svg width="14" height="20" viewBox="0 0 14 20"><path fill="#fff" d="M7 0a7 7 0 0 0-7 7c0 5 7 13 7 13s7-8 7-13a7 7 0 0 0-7-7zm0 10a3 3 0 1 1 0-6 3 3 0 0 1 0 6z"/></svg>
    <div><strong>Hearthline Insurance</strong><br><span class="sub">Lorem Office, 48 West Lorem Street,<br>Ipsum 221100, NY, USA 60611</span></div>
  </div>
  <div class="contact-row" style="top:150px">
    <svg width="16" height="16" viewBox="0 0 24 24"><path fill="#fff" d="M6.6 10.8a15 15 0 0 0 6.6 6.6l2.2-2.2a1 1 0 0 1 1-.25 11.4 11.4 0 0 0 3.6.57 1 1 0 0 1 1 1V20a1 1 0 0 1-1 1A17 17 0 0 1 3 4a1 1 0 0 1 1-1h3.5a1 1 0 0 1 1 1c0 1.25.2 2.45.57 3.57a1 1 0 0 1-.25 1z"/></svg>
    <span>123-555-0172</span>
  </div>
  <div class="contact-row" style="top:200px">
    <svg width="16" height="12" viewBox="0 0 16 12"><rect width="16" height="12" fill="#fff"/><path d="M0 0l8 6 8-6" fill="none" stroke="#2a2e35" stroke-width="1.4"/></svg>
    <span>info@hearthlineinsurance.com</span>
  </div>
</div>

<section class="inquiry abs">
  <h4 class="inquiry-title">Quick Inquiry</h4>
  <div class="inquiry-rule"></div>
  <div class="field" style="top:128px">Your Name</div>
  <div class="field" style="top:172px">Phone</div>
  <div class="field" style="top:216px">Email</div>
  <div class="field" style="top:260px">Message</div>
  <div class="submit">Submit</div>
</section>

<div class="bottom-bar abs">
  <p class="copyright">Copyright © 2018 Hearthline Insurance. All Right Reserved.</p>
  <div class="social"><span></span><span></span><span></span></div>
</div>

</body>
</html>
```